MRT Property - Business Cards

Looking for a business card & general letterhead, signage etc design for our new logo.

Colours:
000a20
0056a2
00b5ef
0088ce
68cef2

Fonts:
Poppins
Karla

Please keep look and feel of new brand - example in the zip package I sent.

```html
<!DOCTYPE html>
<html lang="en">
<head>
<meta charset="utf-8">
<title>MRT Property – Business Cards</title>
<link rel="stylesheet" href="https://fonts.googleapis.com/css2?family=Poppins:wght@500;600&family=Karla:wght@400;500&family=Montserrat:wght@400;500&display=swap">
<style>
  :root {
    --navy: #000a20;
    --card-navy: #12162b;
    --royal: #0056a2;
    --cyan: #00b5ef;
    --mid-blue: #0088ce;
    --sky: #68cef2;
    --ink: #1a1a1a;
    --paper: #ffffff;
    --stage: #e9ebef;
  }
  * { margin: 0; padding: 0; box-sizing: border-box; }
  html, body { width: 1200px; height: 931px; overflow: hidden; }
  body { background: var(--stage); position: relative; font-family: "Montserrat", "Karla", sans-serif; }

  .card {
    position: absolute;
    width: 720px;
    height: 411px;
    border-radius: 22px;
    box-shadow: 0 10px 28px rgba(0, 10, 32, 0.18);
    overflow: hidden;
  }
  .card--front { left: 60px; top: 40px; background: var(--card-navy); }
  .card--back { left: 420px; top: 480px; background: var(--paper); }

  .wordmark {
    position: absolute;
    display: flex;
    align-items: center;
    gap: 18px;
    font-family: "Poppins", sans-serif;
    font-weight: 600;
    white-space: nowrap;
  }
  .wordmark__dot { border-radius: 50%; background: var(--cyan); flex: none; }
  .card--front .wordmark { left: 50%; top: 50%; transform: translate(-50%, -50%); color: var(--paper); font-size: 64px; }
  .card--front .wordmark__dot { width: 58px; height: 58px; }
  .card--back .wordmark { left: 250px; top: 58px; color: var(--royal); font-size: 50px; }
  .card--back .wordmark__dot { width: 46px; height: 46px; }

  .holder { position: absolute; left: 40px; top: 222px; }
  .holder__name { font-family: "Karla", sans-serif; font-weight: 400; font-size: 34px; color: var(--royal); line-height: 1; }
  .holder__title { font-size: 15px; color: var(--ink); margin-top: 6px; letter-spacing: 0.2px; }

  .rule { position: absolute; left: 40px; right: 36px; top: 292px; height: 2px; background: var(--royal); }

  .address { position: absolute; right: 40px; top: 238px; text-align: right; font-size: 15px; color: var(--ink); line-height: 1.45; }

  .contacts { position: absolute; left: 40px; top: 306px; list-style: none; }
  .contacts li { display: flex; align-items: center; gap: 12px; font-size: 16px; color: var(--ink); height: 30px; }
  .contacts svg { width: 18px; height: 18px; flex: none; fill: var(--royal); }
</style>
</head>
<body>

<section class="card card--front" aria-label="Business card front">
  <div class="wordmark"><span class="wordmark__dot"></span>MRT Property</div>
</section>

<section class="card card--back" aria-label="Business card back">
  <div class="wordmark"><span class="wordmark__dot"></span>MRT Property</div>

  <div class="holder">
    <p class="holder__name">Daniel Brooks</p>
    <p class="holder__title">Managing Director</p>
  </div>

  <p class="address">410 Maple Ridge Ave Suite<br>220 Dayton Ohio 45402</p>

  <div class="rule"></div>

  <ul class="contacts">
    <li>
      <svg viewBox="0 0 24 24" aria-hidden="true"><path d="M6.6 10.8a15.1 15.1 0 0 0 6.6 6.6l2.2-2.2a1 1 0 0 1 1-.25 11.4 11.4 0 0 0 3.6.57 1 1 0 0 1 1 1V20a1 1 0 0 1-1 1A17 17 0 0 1 3 4a1 1 0 0 1 1-1h3.5a1 1 0 0 1 1 1c0 1.25.2 2.45.57 3.57a1 1 0 0 1-.25 1z"/></svg>
      1 (555) 014-2297
    </li>
    <li>
      <svg viewBox="0 0 24 24" aria-hidden="true"><path d="M2 5h20v14H2z" fill="none"/><path d="M3 5h18a1 1 0 0 1 1 1v.4l-10 6.2L2 6.4V6a1 1 0 0 1 1-1zm-1 3.7 10 6.2 10-6.2V18a1 1 0 0 1-1 1H3a1 1 0 0 1-1-1z"/></svg>
      info@mrtproperty.com
    </li>
    <li>
      <svg viewBox="0 0 24 24" aria-hidden="true"><path d="M12 2a10 10 0 1 0 0 20 10 10 0 0 0 0-20zm6.9 6h-2.9a15.7 15.7 0 0 0-1.4-3.6A8 8 0 0 1 18.9 8zM12 4c.8 1.2 1.5 2.5 1.9 4h-3.8c.4-1.5 1.1-2.8 1.9-4zM4.3 14a8 8 0 0 1 0-4h3.4a16.5 16.5 0 0 0 0 4zm.8 2h2.9c.3 1.3.8 2.5 1.4 3.6A8 8 0 0 1 5.1 16zM8 8H5.1a8 8 0 0 1 4.3-3.6C8.8 5.5 8.3 6.7 8 8zm4 12c-.8-1.2-1.5-2.5-1.9-4h3.8c-.4 1.5-1.1 2.8-1.9 4zm2.3-6H9.7a14.7 14.7 0 0 1 0-4h4.6a14.7 14.7 0 0 1 0 4zm.3 5.6c.6-1.1 1.1-2.3 1.4-3.6h2.9a8 8 0 0 1-4.3 3.6zm1.7-5.6a16.5 16.5 0 0 0 0-4h3.4a8 8 0 0 1 0 4z"/></svg>
      www.mrtproperty.com
    </li>
  </ul>
</section>

</body>
</html>
```